Brightmoor Talent company

We require a website for job recruitment company called "Brightmoor Talent"
Our company is specialising in recruitment of skilled labour from Sri Lanka into Australian market.
We would like to include a job advertising plugin where jobs can be listed and applied for .
COPYWRITING MUST BE INCLUDED !

Industry/Entity Type

Recruitment

Coding

Coded - Design and coding required

Number of Pages Required

5+ page

Colors

Designer to choose colors to be used in the design.

```html
<!DOCTYPE html>
<html lang="en">
<head>
<meta charset="utf-8">
<title>Contact us – Brightmoor Talent</title>
<link rel="stylesheet" href="https://fonts.googleapis.com/css2?family=Arimo:wght@400;700&display=swap">
<style>
  :root {
    --ink: #4a4a4a;
    --white: #ffffff;
    --night: #272a33;
    --slate: #878d99;
    --mist: #f1f1f1;
    --map: #e3e3e3;
    --sun: #efc40f;
    --link: #3a7fd0;
    --base: #333333;
    --hero-a: #5d6470;
    --hero-b: #7a6a55;
    --dot: #1f57a8;
  }
  * { box-sizing: border-box; margin: 0; padding: 0; }
  html, body { width: 683px; height: 1200px; overflow: hidden; }
  body { position: relative; font-family: "Arimo", Arial, sans-serif; background: var(--white); color: var(--ink); }
  .abs { position: absolute; }

  .site-header { left: 0; top: 0; width: 683px; height: 36px; background: var(--white); }
  .brand { font-weight: 700; font-size: 14px; color: var(--ink); white-space: nowrap; display: flex; align-items: center; gap: 6px; }
  .brand-dot { width: 9px; height: 9px; border-radius: 50%; background: var(--dot); }
  .site-header .brand { left: 47px; top: 10px; }
  .nav { right: 61px; top: 12px; display: flex; gap: 20px; font-size: 8.5px; font-weight: 700; color: var(--ink); }

  .hero { left: 0; top: 36px; width: 683px; height: 318px; background: linear-gradient(160deg, var(--hero-a) 0%, #6b6f76 45%, var(--hero-b) 100%); }
  .hero-title { left: 80px; top: 96px; font-size: 37px; font-weight: 700; color: var(--white); letter-spacing: 0.3px; }
  .hero-text { left: 64px; top: 188px; width: 200px; text-align: center; font-size: 10.3px; line-height: 16.5px; color: var(--white); }

  .contact-band { left: 0; top: 354px; width: 683px; height: 423px; background: var(--night); }
  .touch { left: 63px; top: 0; width: 204px; height: 423px; color: var(--white); }
  .touch h2 { position: absolute; left: -10px; width: 224px; top: 26px; text-align: center; font-size: 18.6px; font-weight: 700; }
  .touch .lede { position: absolute; left: -10px; width: 224px; top: 59px; text-align: center; font-size: 10.3px; line-height: 16.5px; }
  .field { position: absolute; left: 0; width: 204px; }
  .field label { display: block; font-size: 8px; font-weight: 700; color: var(--white); }
  .field .input { margin-top: 10px; padding-left: 6px; height: 19px; font-size: 8px; color: #b9bcc3; border-bottom: 1px solid var(--white); }
  .field .area { margin-top: 8px; height: 61px; border-bottom: 1px solid var(--white); }
  .submit { position: absolute; left: 0; top: 311px; width: 204px; height: 28px; border-radius: 3px; background: var(--sun); color: var(--white); font-size: 8px; font-weight: 700; letter-spacing: 1.5px; display: flex; align-items: center; justify-content: center; }

  .offices { left: 283px; top: 354px; width: 353px; height: 423px; background: var(--slate); color: var(--white); }
  .offices h2 { position: absolute; left: 0; width: 353px; top: 25px; text-align: center; font-size: 18.6px; font-weight: 700; }
  .offices .lede { position: absolute; left: 0; width: 353px; top: 55px; text-align: center; font-size: 11.4px; }
  .card-photo { left: 94px; top: 131px; width: 243px; height: 180px; background: linear-gradient(135deg, #c9b3a4 0%, #8d8d91 50%, #3c3c40 100%); border-radius: 2px; }
  .city { position: absolute; top: 330px; width: 104px; }
  .city h3 { font-size: 10px; font-weight: 700; }
  .city p { margin-top: 10px; font-size: 7.8px; line-height: 13px; }

  .locations { left: 0; top: 777px; width: 683px; height: 331px; background: var(--mist); }
  .region { left: 47px; top: 37px; width: 295px; height: 258px; background: linear-gradient(180deg, #8d95a2 0%, #b3b9c3 40%, #f7f7f8 100%); }
  .region h2 { position: absolute; left: 31px; top: 93px; font-size: 18.6px; font-weight: 700; color: #1c1c1c; }
  .region p { position: absolute; left: 31px; top: 123px; font-size: 8.5px; line-height: 13px; color: #1c1c1c; }
  .region a { color: var(--link); text-decoration: none; }
  .map { left: 342px; top: 37px; width: 294px; height: 258px; background: var(--map); }

  .site-footer { left: 0; top: 1108px; width: 683px; height: 43px; background: var(--white); }
  .site-footer .brand { left: 47px; top: 13px; font-size: 15px; }
  .social { right: 55px; top: 4px; display: flex; gap: 5px; }
  .social span { width: 29px; height: 29px; border-radius: 50%; display: block; }
  .base { left: 0; top: 1151px; width: 683px; height: 49px; background: var(--base); }
</style>
</head>
<body>
  <header class="site-header abs">
    <div class="brand abs"><span class="brand-dot"></span>Brightmoor Talent</div>
    <nav class="nav abs"><span>Home</span><span>Work</span><span>About us</span><span>Contact us</span></nav>
  </header>

  <section class="hero abs" role="img" aria-label="Photo of hands holding a phone beside a laptop on a wooden desk">
    <h1 class="hero-title abs">CONTACT US</h1>
    <p class="hero-text abs">Skilled workers from Sri Lanka, matched with Australian employers. Reach out and our team will reply within a day.</p>
  </section>

  <section class="contact-band abs">
    <div class="touch abs">
      <h2>Get in Touch</h2>
      <p class="lede">Have an inquiry or some feedback for us? Fill out the form below to contact our team.</p>
      <div class="field" style="top:109px"><label>Name</label><div class="input">Enter your Name</div></div>
      <div class="field" style="top:165px"><label>Email</label><div class="input">Enter a valid email address</div></div>
      <div class="field" style="top:221px"><label>How can we help?</label><div class="area"></div></div>
      <div class="submit">SUBMIT</div>
    </div>
  </section>

  <section class="offices abs">
    <h2>Contact Us</h2>
    <p class="lede">Any questions or remarks? Just write us a message!</p>
    <div class="card-photo abs" role="img" aria-label="Photo of a hand in a suit holding up a business card"></div>
    <div class="city" style="left:20px"><h3>Sydney</h3><p>18 Harbourline Rd, Pyrmont NSW 2009</p></div>
    <div class="city" style="left:128px"><h3>Melbourne</h3><p>72 Laneway St, Melbourne VIC 3000</p></div>
    <div class="city" style="left:235px"><h3>Los Angeles</h3><p>215 Shoreline Ave, Venice CA 90291, USA</p></div>
  </section>

  <section class="locations abs">
    <div class="region abs">
      <h2>AUSTRALIA</h2>
      <p>128 Kestrel St, Sydney NSW 2000<br>02 5550 1842<br><a href="#">hello@brightmoortalent.com</a></p>
    </div>
    <div class="map abs" role="img" aria-label="Map showing the Sydney office location"></div>
  </section>

  <footer class="site-footer abs">
    <div class="brand abs"><span class="brand-dot"></span>Brightmoor Talent</div>
    <div class="social abs">
      <span style="background:#3b5998" aria-label="Social link"></span>
      <span style="background:#4aa3e8" aria-label="Social link"></span>
      <span style="background:#c13584" aria-label="Social link"></span>
    </div>
  </footer>
  <div class="base abs"></div>
</body>
</html>
```